Business card design

Hi,
I need to have a business card design based on the current logo.
If competitive I not put it out to everyone.

It can be single of double sided

Target Market(s)

Food businesses

Industry/Entity Type

Food Manufacturing

Contact Information for Business Card

Details will on card will be as follows Name = Marcus Bell Email = Marcus@PanHearth.com.au Phone = 0418563207 Address = 57 Larkin Street , Fortitude Valley QLD 4006 Australia

Font styles to use
Other font styles liked:
• based on two fonts - Adelle & Museo

Requirements
Must have
• Based on the on switch concept

```html
<!DOCTYPE html>
<html lang="en">
<head>
<meta charset="utf-8">
<title>PanHearth Business Card</title>
<link rel="stylesheet" href="https://fonts.googleapis.com/css2?family=Montserrat:wght@400;700&family=Zilla+Slab:wght@500&display=swap">
<style>
  :root {
    --backdrop: #3b3b3b;
    --card: #1a1a1a;
    --red: #ec2a4a;
    --white: #f4f4f4;
    --muted: #dcdcdc;
    --deep: #2a2a2a;
  }
  * { box-sizing: border-box; margin: 0; padding: 0; }
  html, body { width: 1200px; height: 801px; overflow: hidden; }
  body {
    background: var(--backdrop);
    font-family: "Montserrat", sans-serif;
    display: flex;
    align-items: center;
    justify-content: center;
    gap: 48px;
  }
  .card {
    position: relative;
    width: 540px;
    height: 310px;
    background: var(--card);
    border-bottom: 3px solid var(--red);
    border-right: 2px solid var(--red);
    box-shadow: 0 14px 30px rgba(0,0,0,.45);
  }
  .brand {
    position: absolute;
    top: 48px;
    left: 0; right: 0;
    display: flex;
    align-items: center;
    justify-content: center;
    gap: 12px;
  }
  .brand-dot {
    width: 26px; height: 26px;
    border-radius: 50%;
    background: var(--red);
  }
  .brand-name {
    font-weight: 700;
    font-size: 40px;
    letter-spacing: 1px;
    color: var(--white);
    line-height: 1;
  }
  .tagline {
    position: absolute;
    top: 102px;
    left: 0; right: 0;
    text-align: center;
    font-family: "Zilla Slab", serif;
    font-weight: 500;
    font-size: 13px;
    color: var(--white);
  }
  .person-name {
    position: absolute;
    top: 150px;
    left: 0; right: 0;
    text-align: center;
    font-weight: 700;
    font-size: 22px;
    letter-spacing: .5px;
    color: var(--red);
  }
  .divider {
    position: absolute;
    top: 200px;
    left: 28px;
    right: 28px;
    height: 1px;
    background: var(--red);
  }
  .contact-list {
    position: absolute;
    left: 28px;
    top: 216px;
    list-style: none;
    font-size: 14px;
    color: var(--muted);
    line-height: 23px;
  }
  .contact-list li { display: flex; align-items: center; gap: 10px; }
  .contact-list svg { width: 12px; height: 12px; fill: var(--red); }
  .address {
    position: absolute;
    right: 28px;
    top: 216px;
    text-align: right;
    font-size: 14px;
    color: var(--muted);
    line-height: 23px;
    font-style: normal;
  }
  .card-back .brand { top: 0; bottom: 0; }
  .card-back .brand-dot { background: var(--deep); width: 40px; height: 40px; }
  .card-back .brand-name { color: var(--deep); font-size: 52px; }
</style>
</head>
<body>
  <section class="card card-front">
    <div class="brand">
      <span class="brand-dot"></span>
      <span class="brand-name">PanHearth</span>
    </div>
    <p class="tagline">Kitchen Supply Made Simple</p>
    <h1 class="person-name">MARCUS BELL</h1>
    <div class="divider"></div>
    <ul class="contact-list">
      <li>
        <svg viewBox="0 0 24 24" aria-hidden="true"><path d="M6.6 10.8a15 15 0 0 0 6.6 6.6l2.2-2.2c.3-.3.7-.4 1-.2 1.1.4 2.3.6 3.6.6.6 0 1 .4 1 1V20c0 .6-.4 1-1 1A17 17 0 0 1 3 4c0-.6.4-1 1-1h3.5c.6 0 1 .4 1 1 0 1.3.2 2.5.6 3.6.1.3 0 .7-.2 1z"/></svg>
        0418563207
      </li>
      <li>
        <svg viewBox="0 0 24 24" aria-hidden="true"><path d="M2 5h20v14H2zm2 2v.5l8 5 8-5V7z"/></svg>
        Marcus@PanHearth.com.au
      </li>
      <li>
        <svg viewBox="0 0 24 24" aria-hidden="true"><circle cx="12" cy="12" r="10"/></svg>
        www.PanHearth.com.au
      </li>
    </ul>
    <address class="address">
      57 Larkin Street<br>
      Kelso Heights<br>
      QLD 4127 Australia
    </address>
  </section>

  <section class="card card-back">
    <div class="brand">
      <span class="brand-dot"></span>
      <span class="brand-name">PanHearth</span>
    </div>
  </section>
</body>
</html>
```